Shopify landing page redesign for the Tidewell Pillow

I am looking for someone with Shopify experience who can redesign our desktop and mobile landing page for the Tidewell Pillow. I am attaching my vision of what I think would convince visitors to purchase. The design should be highly focused on features and benefits and it needs to show how it solves our customer’s sleeping problems. It should also be designed with minimal distractions. Blue color is RGB: 0, 176, 24 or HEX: #00B0F0 I am looking for fast delivery.

```html
<!DOCTYPE html>
<html lang="en">
<head>
<meta charset="utf-8">
<title>Tidewell Pillow – Adjust it. Fluff it. Love it.</title>
<link href="https://fonts.googleapis.com/css2?family=Bebas+Neue&family=Poppins:ital,wght@0,400;0,500;0,600;1,400;1,500&display=swap" rel="stylesheet">
<style>
:root{
  --blue:#1a9be6;
  --blue-light:#5cbde6;
  --blue-deep:#0f8ee4;
  --ink:#1e1e1e;
  --text:#333;
  --white:#fff;
  --footer:#111214;
  --card:#f6f7f8;
}
*{box-sizing:border-box;margin:0;padding:0}
html,body{width:1200px;height:4633px;overflow:hidden}
body{font-family:"Poppins",sans-serif;color:var(--text);background:var(--white)}
.page{position:relative;width:1200px;height:4633px;overflow:hidden}
.abs{position:absolute}
.display{font-family:"Bebas Neue",sans-serif;font-weight:400;color:var(--ink);line-height:1.05;letter-spacing:.5px}
.accent{color:var(--blue)}
.btn{position:absolute;display:flex;align-items:center;justify-content:center;border-radius:40px;font-family:"Bebas Neue",sans-serif;font-size:15px;letter-spacing:.4px}
.btn-blue{background:var(--blue);color:var(--white)}
.btn-white{background:var(--white);color:var(--ink)}
.brand{font-family:"Poppins",sans-serif;font-weight:600;font-size:26px;color:var(--white);display:flex;align-items:center;gap:10px}
.brand .dot{width:16px;height:16px;border-radius:50%;background:var(--white)}
.photo{position:absolute}

/* header */
.site-header{left:0;top:0;width:1200px;height:126px;background:var(--blue)}
.site-header .brand{position:absolute;left:112px;top:44px}

/* hero */
.hero{left:0;top:126px;width:1200px;height:520px}
.hero .photo{left:560px;top:0;width:640px;height:520px;background:linear-gradient(110deg,#f4f4f4 0%,#eae3dc 45%,#dcc9b3 75%,#f1eeea 100%)}
.hero .stars{left:113px;top:76px;color:var(--blue);font-size:24px;letter-spacing:2px}
.hero .quote{left:113px;top:114px;font-size:16px}
.hero h1{left:113px;top:152px;font-size:56px}
.hero .lead{left:113px;top:224px;width:440px;font-size:15px;line-height:2}
.hero .btn{left:113px;top:306px;width:180px;height:46px}
.hero .note{left:113px;top:374px;font-size:11px}

/* perks */
.perk{top:715px;width:218px;height:171px;border-radius:36px 36px 14px 14px;background:linear-gradient(180deg,var(--blue-light),var(--blue));color:var(--white);display:flex;flex-direction:column;align-items:center;justify-content:center;text-align:center;font-size:20px;line-height:1.3;gap:12px}

/* designed */
.designed .photo{left:54px;top:954px;width:486px;height:495px;border-radius:50%;background:radial-gradient(circle at 50% 40%,#f2f2f2 0 30%,#c99a7a 31% 42%,var(--blue-light) 43%,var(--blue) 100%)}
.designed h2{left:621px;top:1004px;font-size:52px}
.checklist{left:621px;top:1146px;list-style:none;font-size:17px}
.checklist li{display:flex;align-items:center;gap:12px;height:58px}

/* seen in */
.seen h2{left:0;top:1548px;width:1200px;text-align:center;font-size:52px}
.badge{top:1636px;height:48px;border-radius:10px;background:#2a2a2a}

/* perfect pillow band */
.band svg{position:absolute;left:0}
.perfect h2{left:0;top:1868px;width:1200px;text-align:center;font-size:54px;color:var(--white)}
.feature{top:1976px;width:232px;height:321px;border-radius:40px 40px 14px 14px;background:var(--white);overflow:hidden}
.feature .pic{height:240px;background:linear-gradient(160deg,#e4e4e4,#c9c9c9)}
.feature .label{height:81px;display:flex;align-items:center;justify-content:center;text-align:center;font-size:18px;color:var(--ink);padding:0 16px;line-height:1.2}
.feature.dark .pic{background:#232323;color:var(--white);font-size:13.5px;line-height:1.8;text-align:center;padding:36px 28px}
.feature.dark .label{color:var(--blue);text-decoration:underline;text-underline-offset:4px}

/* reviews */
.reviews h2{left:113px;top:2518px;font-size:52px}
.review{display:flex;flex-direction:column;justify-content:center;align-items:center;text-align:center;font-style:italic}
.review.side{top:2682px;height:180px;background:var(--card);border-radius:12px;box-shadow:0 2px 10px rgba(0,0,0,.08);font-size:15px;line-height:1.55;color:var(--ink)}
.review.main{left:376px;top:2644px;width:454px;height:243px;background:linear-gradient(180deg,var(--blue-light),var(--blue));border-radius:14px;color:var(--white);font-size:19px;line-height:1.55;padding:0 42px}
.review .who{font-style:normal;font-weight:600;color:var(--blue);margin-top:14px;font-size:15px}
.review.main .who{color:var(--white);font-size:19px;margin-top:10px}
.review.main .stars{font-style:normal;letter-spacing:6px;font-size:20px;margin-bottom:14px}
.dots{left:0;top:2924px;width:1200px;display:flex;justify-content:center;gap:10px;align-items:center}
.dots span{width:13px;height:13px;border-radius:50%;background:#999}
.dots span.on{width:26px;height:16px;border-radius:10px;background:var(--blue)}

/* warranty */
.warranty .photo{left:594px;top:3046px;width:606px;height:406px;background:linear-gradient(90deg,var(--blue) 0%,#dfe6ee 22%,#f4f4f4 60%,#b98e6e 100%)}
.warranty .title{left:0;top:3226px;width:702px;text-align:center;font-size:50px;color:var(--white)}
.warranty .body{left:150px;top:3300px;width:402px;text-align:center;font-size:16px;line-height:1.7;color:var(--white)}

/* ready */
.ready .photo{left:108px;top:3528px;width:432px;height:414px;border-radius:50%;background:radial-gradient(circle at 50% 45%,#f4f4f4 0 34%,#b88a6c 35% 44%,var(--blue-light) 45%,var(--blue) 100%)}
.ready h2{left:599px;top:3632px;font-size:52px}
.ready p{left:599px;top:3750px;font-size:16px}
.ready .btn{left:599px;top:3807px;width:216px;height:45px}

/* guarantee */
.guarantee{left:0;top:4000px;width:1200px;height:437px;background:var(--blue)}
.guarantee .photo{left:0;top:0;width:640px;height:437px;background:linear-gradient(90deg,#d9c3ad 0%,#ececec 45%,#e6ecf1 80%,var(--blue) 100%)}
.guarantee .title{left:599px;top:118px;font-size:52px;color:var(--white)}
.guarantee .body{left:599px;top:192px;width:500px;font-size:17px;line-height:1.85;color:var(--white)}
.guarantee .btn{left:599px;top:288px;width:173px;height:43px}

/* footer */
.site-footer{left:0;top:4437px;width:1200px;height:196px;background:var(--footer)}
.site-footer .brand{position:absolute;left:104px;top:82px}
.socials{position:absolute;left:893px;top:64px;display:flex;gap:10px}
.socials span{width:30px;height:30px;border-radius:50%;background:var(--white)}
.copy{position:absolute;left:664px;top:120px;font-size:15px;color:var(--white)}
</style>
</head>
<body>
<div class="page">

  <header class="abs site-header">
    <div class="brand"><span class="dot"></span>Tidewell Pillow</div>
    <a class="btn btn-white" style="left:965px;top:40px;width:120px;height:43px">Buy Now</a>
  </header>

  <section class="abs hero">
    <div class="photo" role="img" aria-label="Woman sleeping peacefully on a white pillow"></div>
    <div class="abs stars">★★★★★</div>
    <p class="abs quote">"Best sleep I've ever had!" - Marla</p>
    <h1 class="abs display">Adjust it. <span class="accent">Fluff it. Love it.</span></h1>
    <p class="abs lead">Shop the adjustable Tidewell Pillow and get the best sleep of your life!</p>
    <a class="btn btn-blue">Try it now &amp; get $20 off</a>
    <p class="abs note">90-DAY MONEY BACK GUARANTEE</p>
  </section>
  <svg class="abs" style="left:0;top:580px" width="1200" height="70" viewBox="0 0 1200 70">
    <path d="M0 20 Q600 70 1200 0 L1200 70 L0 70Z" fill="#fff"/>
    <path d="M0 14 Q600 58 1200 -6 L1200 4 Q600 80 0 30Z" fill="var(--blue)"/>
  </svg>

  <section class="perks">
    <div class="abs perk" style="left:194px">
      <svg width="80" height="50" viewBox="0 0 80 50" fill="none" stroke="#fff" stroke-width="2"><rect x="2" y="4" width="48" height="32" rx="2"/><path d="M50 14h16l10 12v10H50"/><circle cx="16" cy="40" r="6"/><circle cx="62" cy="40" r="6"/><text x="8" y="25" fill="#fff" stroke="none" font-family="Poppins" font-size="12">FREE</text></svg>
      Free Shipping
    </div>
    <div class="abs perk" style="left:491px">
      <svg width="64" height="56" viewBox="0 0 64 56" fill="none" stroke="#fff" stroke-width="2"><circle cx="40" cy="20" r="14"/><text x="35" y="25" fill="#fff" stroke="none" font-family="Poppins" font-size="14">$</text><path d="M4 40h14l12 6 20-10M4 52h18l28-6"/></svg>
      90 - Night Free<br>Trial
    </div>
    <div class="abs perk" style="left:788px">
      <svg width="50" height="56" viewBox="0 0 50 56" fill="none" stroke="#fff" stroke-width="2.5"><path d="M25 3 L46 11 V27 C46 40 37 49 25 53 C13 49 4 40 4 27 V11Z"/><path d="M16 28l7 7 12-13"/></svg>
      3-Years Warranty
    </div>
  </section>

  <section class="designed">
    <div class="photo" role="img" aria-label="Smiling woman hugging a quilted Tidewell Pillow"></div>
    <h2 class="abs display">Designed for the <span class="accent">sleep<br>you deserve!</span></h2>
    <ul class="abs checklist">
      <li><svg width="22" height="22" viewBox="0 0 22 22" fill="none" stroke="#222" stroke-width="1.6"><circle cx="11" cy="11" r="9.5"/><path d="M6.5 11.5l3 3 6-6.5"/></svg>Fully adjustable for all sleep positions</li>
      <li><svg width="22" height="22" viewBox="0 0 22 22" fill="none" stroke="#222" stroke-width="1.6"><circle cx="11" cy="11" r="9.5"/><path d="M6.5 11.5l3 3 6-6.5"/></svg>Memory foam blend relieves neck pain</li>
      <li><svg width="22" height="22" viewBox="0 0 22 22" fill="none" stroke="#222" stroke-width="1.6"><circle cx="11" cy="11" r="9.5"/><path d="M6.5 11.5l3 3 6-6.5"/></svg>Maintains shape - no more flipping</li>
      <li><svg width="22" height="22" viewBox="0 0 22 22" fill="none" stroke="#222" stroke-width="1.6"><circle cx="11" cy="11" r="9.5"/><path d="M6.5 11.5l3 3 6-6.5"/></svg>Stay cool with ChillWeave Technology™</li>
      <li><svg width="22" height="22" viewBox="0 0 22 22" fill="none" stroke="#222" stroke-width="1.6"><circle cx="11" cy="11" r="9.5"/><path d="M6.5 11.5l3 3 6-6.5"/></svg>Soft hypoallergenic cover for sensitive skin</li>
    </ul>
  </section>

  <section class="seen">
    <h2 class="abs display"><span class="accent">As seen</span> in</h2>
    <div class="abs badge" style="left:198px;width:52px;border-radius:50%"></div>
    <div class="abs badge" style="left:322px;width:80px;background:var(--blue)"></div>
    <div class="abs badge" style="left:462px;width:74px"></div>
    <div class="abs badge" style="left:578px;width:94px"></div>
    <div class="abs badge" style="left:770px;width:58px"></div>
    <div class="abs badge" style="left:934px;width:70px"></div>
  </section>

  <section class="band perfect">
    <svg style="top:1719px" width="1200" height="740" viewBox="0 0 1200 740">
      <defs><linearGradient id="bandFill" x1="0" y1="0" x2="0" y2="1"><stop offset="0" stop-color="#5cbde6"/><stop offset="1" stop-color="#1592e6"/></linearGradient></defs>
      <path d="M0 0 Q600 130 1200 10 L1200 738 Q700 610 0 690Z" fill="url(#bandFill)"/>
    </svg>
    <h2 class="abs display">The perfect pillow for a better nights sleep</h2>
    <div class="abs feature" style="left:59px"><div class="pic" role="img" aria-label="Woman asleep on the pillow"></div><div class="label">Adjustable for all sleepers</div></div>
    <div class="abs feature dark" style="left:342px"><div class="pic">Engineered to deliver better sleep with TIDEcomfort Fill, a special blend of gel-infused memory foam and microfiber clusters. Cradles your head, neck</div><div class="label">Cloudlike comfort</div></div>
    <div class="abs feature" style="left:625px"><div class="pic" role="img" aria-label="Two stacked pillows with foam fill"></div><div class="label">Stay cooler</div></div>
    <div class="abs feature" style="left:909px"><div class="pic" role="img" aria-label="Woman hugging a pillow"></div><div class="label">Sensitive skin safe</div></div>
  </section>

  <section class="reviews">
    <h2 class="abs display">What our <span class="accent">customer are saying...</span></h2>
    <div class="abs review side" style="left:59px;width:330px;padding:0 40px 0 30px">I used to wake up with neck pain almost every day—until I bought this pillow. It's perfectly supportive without being too firm.<span class="who">— Nina Farrow</span></div>
    <div class="abs review side" style="left:818px;width:325px;padding:0 30px 0 40px">I was hesitant to spend more on a pillow, but now I totally get it. This is luxury-level comfort. It keeps just for me.<span class="who">— Owen Price</span></div>
    <div class="abs review main"><span class="stars">★★★★★</span>'I'm in love with this pillow! Since I started using it, my sleep has been incredibly restful. It's like sleeping on a fluffy cloud!<span class="who">— Leah P.</span></div>
    <div class="abs dots"><span></span><span class="on"></span><span></span></div>
  </section>

  <section class="band warranty">
    <svg style="top:2979px" width="1200" height="474" viewBox="0 0 1200 474">
      <path d="M0 0 Q300 80 594 67 L1200 67 L1200 474 L0 474Z" fill="var(--blue)"/>
    </svg>
    <div class="photo" role="img" aria-label="Two white pillows stacked on a bed"></div>
    <svg class="abs" style="left:323px;top:3136px" width="56" height="62" viewBox="0 0 50 56" fill="none" stroke="#fff" stroke-width="2.5"><path d="M25 3 L46 11 V27 C46 40 37 49 25 53 C13 49 4 40 4 27 V11Z"/><path d="M16 28l7 7 12-13"/></svg>
    <h2 class="abs display title">3-Year Warranty</h2>
    <p class="abs body">Sleep soundly knowing every Tidewell Pillow comes with a 3-year warranty.</p>
  </section>

  <section class="ready">
    <div class="photo" role="img" aria-label="Woman holding stacked pillows with foam fill beside her"></div>
    <h2 class="abs display">Ready for the <span class="accent">sleep you<br>deserve?</span></h2>
    <p class="abs">Ships fast. Full refund if not delighted.</p>
    <a class="btn btn-blue">Start sleeping better tonight</a>
  </section>

  <section class="abs guarantee">
    <div class="photo" role="img" aria-label="Woman sleeping on a Tidewell Pillow"></div>
    <h2 class="abs display title">90-Night Risk-Free Guarantee</h2>
    <p class="abs body">Try the Tidewell Pillow at home for 90-nights, if you don't absolutely love it, you can return it for a full refund.</p>
    <a class="btn btn-white">Try it now &amp; get $20 off</a>
  </section>

  <footer class="abs site-footer">
    <div class="brand"><span class="dot"></span>Tidewell Pillow</div>
    <div class="socials"><span></span><span></span><span></span><span></span><span></span></div>
    <p class="copy">Copyrights @ 2025 Tidewell Pillow - All Rights Reserved</p>
  </footer>

</div>
</body>
</html>
```